A design led business card for the construction industry

High-end business card to match logo. White logo on dark grey/off black to the front. Matching dark font on white to back, possibly with logo design again.

We offer construction and project management services to commercial and private clients in the UK. Projetcs range from newbuilds, conversion of listed buildings and refurbishments and extensions of existing homes. Our focus is on quality and attention to detail using the highest skills.

Contact Information for Business Card

Name; Dorian Keble BSc
Position; Project Manager
Mobile; 07962 408 175
Tel; 01632 960457
email; dorian@stonevale.co.uk
web; www.stonevale.co.uk
Address; Ashcombe on Tarn, KX4 7PW

Colors

Designer to choose only greyscale colors for use in the design.

Requirements
Must have
• To include the below description of the business,

CONSTRUCTION - PROJECT MANAGEMENT
Nice to have
• The posibility of the top back of the card being used as a ruler. So will have a measurement to scale in mm or an architect scale of 1:50
Should not have
• Should not be portrait

```html
<!DOCTYPE html>
<html lang="en">
<head>
<meta charset="utf-8">
<title>Stonevale Business Card</title>
<link href="https://fonts.googleapis.com/css2?family=Arimo:wght@400;700&display=swap" rel="stylesheet">
<style>
  :root {
    --backdrop: #1c1c1c;
    --backdrop-edge: #0c0c0c;
    --card-dark: #2a2a2b;
    --card-light: #ffffff;
    --ink-light: #ffffff;
    --ink-dark: #1b1b1b;
    --tick: #bdbdbd;
  }
  * { margin: 0; padding: 0; box-sizing: border-box; }
  html, body { width: 1200px; height: 1015px; overflow: hidden; }
  body {
    background: radial-gradient(ellipse at 50% 40%, var(--backdrop) 0%, var(--backdrop-edge) 100%);
    font-family: "Arimo", Arial, sans-serif;
    position: relative;
  }
  .card {
    position: absolute;
    width: 620px;
    height: 360px;
    box-shadow: 0 18px 40px rgba(0,0,0,0.6);
    overflow: hidden;
  }
  .card--front { left: 90px; top: 110px; background: var(--card-dark); color: var(--ink-light); }
  .card--back { left: 490px; top: 545px; background: var(--card-dark); display: flex; }

  .ruler { position: absolute; left: 0; top: 0; width: 620px; height: 26px; }

  .brand {
    display: flex;
    flex-direction: column;
    align-items: center;
  }
  .brand__mark {
    width: 86px; height: 86px;
    border: 4px solid currentColor;
  }
  .brand__name {
    font-weight: 400;
    letter-spacing: 0.55em;
    margin-right: -0.55em;
    text-transform: uppercase;
  }
  .card--front .brand { position: absolute; left: 0; right: 0; top: 92px; }
  .card--front .brand__name { font-size: 30px; margin-top: 34px; }
  .tagline {
    font-size: 12.5px;
    letter-spacing: 0.04em;
    margin-top: 18px;
  }

  .contact {
    width: 285px;
    padding: 118px 0 0 42px;
    color: var(--ink-light);
  }
  .contact__name { font-size: 17px; font-weight: 700; text-transform: uppercase; }
  .contact__name span { font-weight: 400; text-transform: none; }
  .contact__role { font-size: 14px; margin-bottom: 10px; }
  .contact__list { list-style: none; font-size: 13.5px; line-height: 19px; }
  .contact__list li { display: flex; align-items: center; gap: 8px; }
  .contact__list svg { width: 13px; height: 13px; flex: none; }
  .contact__address { font-size: 14px; margin-top: 14px; white-space: nowrap; }

  .card__panel {
    flex: 1;
    background: var(--card-light);
    color: var(--ink-dark);
    display: flex;
    align-items: center;
    justify-content: center;
  }
  .card__panel .brand__mark { width: 74px; height: 74px; border-width: 3px; }
  .card__panel .brand__name { font-size: 21px; margin-top: 28px; }
</style>
</head>
<body>

<section class="card card--front">
  <svg class="ruler" viewBox="0 0 620 26" aria-hidden="true">
    <defs>
      <pattern id="mm-ticks" width="72.9" height="26" patternUnits="userSpaceOnUse">
        <g stroke="var(--tick)" stroke-width="1">
          <line x1="0.5" y1="0" x2="0.5" y2="22"/>
          <line x1="7.8" y1="0" x2="7.8" y2="8"/>
          <line x1="15.1" y1="0" x2="15.1" y2="8"/>
          <line x1="22.4" y1="0" x2="22.4" y2="8"/>
          <line x1="29.7" y1="0" x2="29.7" y2="8"/>
          <line x1="37" y1="0" x2="37" y2="14"/>
          <line x1="44.2" y1="0" x2="44.2" y2="8"/>
          <line x1="51.5" y1="0" x2="51.5" y2="8"/>
          <line x1="58.8" y1="0" x2="58.8" y2="8"/>
          <line x1="66.1" y1="0" x2="66.1" y2="8"/>
        </g>
      </pattern>
    </defs>
    <rect width="620" height="26" fill="url(#mm-ticks)"/>
  </svg>
  <div class="brand">
    <div class="brand__mark"></div>
    <div class="brand__name">Stonevale</div>
    <div class="tagline">CONSTRUCTION - PROJECT MANAGEMENT</div>
  </div>
</section>

<section class="card card--back">
  <div class="contact">
    <p class="contact__name">Dorian Keble <span>BSc</span></p>
    <p class="contact__role">Project Manager</p>
    <ul class="contact__list">
      <li>
        <svg viewBox="0 0 14 14" fill="none" stroke="#fff" stroke-width="1.4"><rect x="3.5" y="1" width="7" height="12" rx="1.2"/><line x1="6" y1="11" x2="8" y2="11"/></svg>
        07962 408 175
      </li>
      <li>
        <svg viewBox="0 0 14 14" fill="none" stroke="#fff" stroke-width="1.4"><path d="M3 1.5l2.2 2.8-1.2 1.5c.8 1.7 2.1 3 3.8 3.8l1.5-1.2 2.8 2.2-1.3 1.9C6 12.3 1.7 8 1.2 3.3z"/></svg>
        01632 960457
      </li>
      <li>
        <svg viewBox="0 0 14 14" fill="none" stroke="#fff" stroke-width="1.4"><rect x="1" y="3" width="12" height="8.5"/><path d="M1 3l6 5 6-5"/></svg>
        dorian@stonevale.co.uk
      </li>
      <li>
        <svg viewBox="0 0 14 14" fill="none" stroke="#fff" stroke-width="1.2"><circle cx="7" cy="7" r="5.8"/><ellipse cx="7" cy="7" rx="2.6" ry="5.8"/><line x1="1.2" y1="7" x2="12.8" y2="7"/></svg>
        www.stonevale.co.uk
      </li>
    </ul>
    <p class="contact__address">Ashcombe on Tarn, KX4 7PW</p>
  </div>
  <div class="card__panel">
    <div class="brand">
      <div class="brand__mark"></div>
      <div class="brand__name">Stonevale</div>
    </div>
  </div>
</section>

</body>
</html>
```